Sell the dream! Property investment proposal document

We are looking for a proposal document which outlines our vision for property development. The purpose of the document is to raise investment from investors - sell the dream!
Brief summary:
Kestrel Dwellings Developments, is an emerging New Zealand property investment company with a focus on providing unique property investment opportunities.
Our expertise and capabilities in architectural modular homes provide us with a remarkable advantage in tackling the development of properties that are typically considered challenging, remote, or uniquely positioned.
Our specialization in this niche sector of property development not only sets us apart from competitors, but also paves the way for lucrative investment opportunities in the New Zealand property market.
Feel free to use any images from www.kestreldwellings.co.nz
Target Market(s)
investors for a unique property development opportunity
Industry/Entity Type
luxury property development in unique locations throughout New Zealand
Colors
Designer to choose only greyscale colors for use in the design.
Look and feel

```html
<!DOCTYPE html>
<html lang="en">
<head>
<meta charset="utf-8">
<title>Kestrel Dwellings Developments – Investment Proposal</title>
<link href="https://fonts.googleapis.com/css2?family=Roboto:wght@300;400;500;700;900&display=swap" rel="stylesheet">
<style>
  :root {
    --canvas: #cbcbcb;
    --cover-dark: #3a3636;
    --page-dark: #2e2c2c;
    --band-dark: #1e1d1d;
    --rule-grey: #8c8c8c;
    --stripe-grey: #9a9a9a;
    --stripe-light: #bdbdbd;
    --ink-light: #f2f2f2;
    --ink-body: #e4e4e4;
    --ink-dark: #141414;
    --white: #ffffff;
  }
  * { box-sizing: border-box; margin: 0; padding: 0; }
  html, body { width: 1200px; height: 591px; overflow: hidden; }
  body { background: var(--canvas); font-family: "Roboto", sans-serif; position: relative; }

  .page { position: absolute; top: 45px; width: 355px; height: 501px; overflow: hidden; }
  .page--cover { left: 38px; background: var(--cover-dark); }
  .page--overview { left: 423px; background: var(--page-dark); border-top: 3px solid var(--rule-grey); }
  .page--summary { left: 806px; background: var(--page-dark); border-top: 3px solid var(--rule-grey); }

  /* Cover */
  .cover-art { position: absolute; inset: 0; }
  .cover-brand { position: absolute; top: 10px; right: 22px; font-weight: 300; font-size: 32px; color: var(--white); letter-spacing: -0.5px; }
  .cover-welcome { position: absolute; left: 133px; top: 350px; font-weight: 700; font-size: 23px; color: var(--ink-dark); }
  .cover-name { position: absolute; left: 131px; top: 372px; font-weight: 900; font-size: 52px; color: var(--ink-dark); letter-spacing: -1px; line-height: 1.3; }
  .cover-phone { position: absolute; left: 133px; top: 449px; display: flex; align-items: center; gap: 8px; }
  .cover-phone__icon { width: 38px; height: 38px; border-radius: 50%; background: var(--cover-dark); display: flex; align-items: center; justify-content: center; }
  .cover-phone__number { font-weight: 700; font-size: 18px; color: var(--ink-dark); }

  /* Inner pages */
  .content { position: absolute; left: 25px; right: 25px; top: 14px; }
  .section-title { font-weight: 500; font-size: 11px; color: var(--ink-light); margin: 0 0 4px; }
  .body-copy { font-weight: 400; font-size: 6.8px; line-height: 13.7px; color: var(--ink-body); text-align: justify; margin-bottom: 2px; }
  .section-rule { border: 0; border-top: 0.6px solid #5a5858; margin: 9px 0 10px; }
  .feature-photo { width: 305px; height: 124px; margin: 8px 0 10px; background: linear-gradient(180deg, #6d7377 0%, #3a3c3d 45%, #2a2b2a 62%, #4d5a43 100%); }
  .section-title--spaced { margin-top: 4px; }

  .footer-band { position: absolute; left: 0; bottom: 0; width: 355px; height: 26px; }
</style>
</head>
<body>

  <!-- Cover -->
  <section class="page page--cover">
    <svg class="cover-art" width="355" height="501" viewBox="0 0 355 501">
      <defs>
        <linearGradient id="heroTone" x1="0" y1="0" x2="0" y2="1">
          <stop offset="0" stop-color="#d8dbdc"/>
          <stop offset="0.4" stop-color="#6f7770"/>
          <stop offset="0.7" stop-color="#2c2c2c"/>
          <stop offset="1" stop-color="#b9bbb8"/>
        </linearGradient>
        <linearGradient id="interiorTone" x1="0" y1="0" x2="1" y2="1">
          <stop offset="0" stop-color="#8d8a84"/>
          <stop offset="1" stop-color="#3d3a37"/>
        </linearGradient>
      </defs>
      <path d="M0,118 L118,42 Q128,36 140,40 L240,88 Q258,98 258,118 L258,255 Q258,270 244,278 L140,330 L0,330 Z" fill="url(#heroTone)" role="img" aria-label="Photograph of a dark timber modular home set among trees and hills"/>
      <path d="M22,130 L145,38 Q155,31 168,34 L262,122 Q276,136 276,150 L276,265" fill="none" stroke="#ffffff" stroke-width="0.7"/>
      <path d="M82,501 L82,390 Q82,370 100,359 L225,285 Q245,274 266,285 L355,338 L355,501 Z" fill="var(--white)"/>
      <path d="M68,251 L103,269 L103,312 L68,333 L29,312 L29,269 Z" fill="url(#interiorTone)" stroke="#ffffff" stroke-width="2.5" role="img" aria-label="Photograph of a living room interior with a view to the hills"/>
    </svg>
    <div class="cover-brand">Kestrel</div>
    <div class="cover-welcome">Welcome To</div>
    <div class="cover-name">Kestrel</div>
    <div class="cover-phone">
      <div class="cover-phone__icon">
        <svg width="18" height="18" viewBox="0 0 24 24"><path fill="#ffffff" d="M6.6 10.8c1.4 2.8 3.8 5.1 6.6 6.6l2.2-2.2c.3-.3.7-.4 1-.2 1.1.4 2.3.6 3.6.6.6 0 1 .4 1 1V20c0 .6-.4 1-1 1C10.6 21 3 13.4 3 4c0-.6.4-1 1-1h3.5c.6 0 1 .4 1 1 0 1.3.2 2.5.6 3.6.1.3 0 .7-.2 1L6.6 10.8z"/></svg>
      </div>
      <div class="cover-phone__number">09 555 0142</div>
    </div>
  </section>

  <!-- Overview & origins -->
  <section class="page page--overview">
    <div class="content">
      <h2 class="section-title">Business Overview</h2>
      <p class="body-copy">Kestrel Dwellings Developments, is an emerging New Zealand property investment company with a focus on providing unique property investment opportunities.</p>
      <p class="body-copy">Our expertise and capabilities in architectural modular homes provide us with a remarkable advantage in tackling the development of properties that are typically considered challenging, remote, or uniquely positioned</p>
      <p class="body-copy">As a company, with 48 employees boasting a wealth of experience in handling complex architectural projects, making us well-equipped to navigate the intricacies and demands of such ventures.</p>
      <p class="body-copy">This advantage allows us to not only execute projects efficiently but also to deliver exceptional results within condensed time frames.</p>
      <p class="body-copy">By capitalizing on our ability to develop difficult, remote, or one-of-a-kind properties swiftly and effectively, Kestrel Dwellings Developments offers investors a rare chance to engage in projects that promise exceptional profitability in the New Zealand property market.</p>
      <p class="body-copy">Our specialization in this niche sector of property development not only sets us apart from competitors, but also paves the way for lucrative investment opportunities in the New Zealand property market.</p>
      <hr class="section-rule">
      <h2 class="section-title">Business Origins</h2>
      <p class="body-copy">Kestrel Dwellings Developments was established with the goal of transforming the property investment market in New Zealand by introducing an innovative approach that centers on architectural modular designs and streamlined project timelines.</p>
      <p class="body-copy">Driven by our enthusiasm for architecture and real estate, we have expanded our successful business model to not only offer financial opportunities for investors but also to expand on our passion for high-end architectural design</p>
      <p class="body-copy">With a wealth of experience accumulated over the past six years in the construction and the property market, we are pivoting to focus solely on our property development initiatives, presenting completed Kestrel projects to the market, in exclusive locations.</p>
      <p class="body-copy">These projects will boast high-quality standards, meticulous attention to detail and landscaping, and creative design elements.</p>
    </div>
    <svg class="footer-band" viewBox="0 0 355 26">
      <rect width="355" height="26" fill="var(--band-dark)"/>
      <polygon points="135,0 150,0 168,26 153,26" fill="var(--stripe-light)"/>
      <polygon points="150,0 160,0 178,26 168,26" fill="var(--stripe-grey)"/>
      <polygon points="160,0 170,0 188,26 178,26" fill="#4a4848"/>
      <polygon points="213,0 216,0 240,26 237,26" fill="var(--stripe-light)"/>
      <polygon points="228,8 355,8 355,19 238,19" fill="var(--stripe-grey)"/>
    </svg>
  </section>

  <!-- Advantage & financials -->
  <section class="page page--summary">
    <div class="content">
      <p class="body-copy">By introducing completed Kestrel properties into the market, we aim to reach a wider audience, catering to individuals who prefer ready-to-occupy homes, over engaging in the design and construction process. This approach also simplifies the financing process for prospective buyers, as established properties are often preferred by financial lenders.</p>
      <div class="feature-photo" role="img" aria-label="Photograph of a single-level dark modular home with a pool and lawn at dusk"></div>
      <h2 class="section-title">Competitive Advantage</h2>
      <p class="body-copy">Our competitive advantage lies in the uniqueness of our property investment opportunities. Unlike traditional real estate companies, we focus on offering properties that are not only profitable but also aesthetically pleasing and unique.</p>
      <p class="body-copy">Additionally, the streamlined and condensed timelines facilitated by our modular approach provide quicker returns on investment.</p>
      <h2 class="section-title section-title--spaced">Financial Summary</h2>
      <p class="body-copy">In terms of financial projections, with each development, we anticipate a profit of 10%-20% which will be project dependent.</p>
      <p class="body-copy">This growth is fueled by the increasing demand for unique property investments in New Zealand and our ability to deliver high-quality services to the market in a condensed time frame, with heavily controlled costs</p>
      <p class="body-copy">New Zealand's property market has been experiencing steady growth over the years, making it an attractive destination for property investors. With its beautiful landscapes and strong economy, New Zealand offers a diverse range of investment opportunities for both local and international investors. The demand for quality properties in prime locations continues to rise, creating a favorable environment for property investment companies like ours that can lean on our modular benefits of being able to reach unique and remote locations.</p>
    </div>
    <svg class="footer-band" viewBox="0 0 355 26">
      <rect width="355" height="26" fill="var(--band-dark)"/>
      <polygon points="135,0 150,0 168,26 153,26" fill="var(--stripe-light)"/>
      <polygon points="150,0 160,0 178,26 168,26" fill="var(--stripe-grey)"/>
      <polygon points="160,0 170,0 188,26 178,26" fill="#4a4848"/>
      <polygon points="213,0 216,0 240,26 237,26" fill="var(--stripe-light)"/>
      <polygon points="228,8 355,8 355,19 238,19" fill="var(--stripe-grey)"/>
    </svg>
  </section>

</body>
</html>
```